Edgey, Modern Air Conditioning Website

Bramble Works
current website - www.kelvaroom.nz
Facebook - www.facebook.com/bramwrk

We really have no idea about webdesign etc we are Engineers not Graphic artists or creative writers. We really just want a edgy, modern website completed on our behalf

We can get pictures of projects as directed or happy for you to use stock images of Talvoro Mecha NZ (Heatpumps) air conditioning and exposed ducting etc

we would like the website to be heavily based on the below website. I like what they have done with both the site and the app but obviously would need to suit Bramble Works, snowflakes heating cooling etc etc Blue and white to match our logo etc

http://parrowbeams.co.nz/

Need links to contact page:
Bramble Works
27 Harlow Crescent
Petone
Wellington

0800 529 174 (0800BRAMWKS)

Marta.k@bramwks.co.nz

BRAMBLE WORKS
SATISFACTION GAURANTEED

WHY CHOOSE BRAMBLE WORKS
EXPERIENCE COUNTS

We have a team of nationally trained and qualified Refrigeration/HVAC/Electrical Engineers and Technicians based in Petone, Wellington offering services to Wellington, Manuwatu and the Wairarapa. We are factory trained and authorised to design, service and install all major brands including Talvoro, Pelnor, Korrowane Electric, Veltrada and Osmelo units. We extend our installation warranty to match that of the manufacturer’s warranty and specialise in our own diagnostics and repair.

SATISFACTION GUARANTEE
We aim to please and I put my name behind our brand! We will take care of your project from start to finish and offer a unique experience with our 100% satisfaction Guarantee*. We will supply and install your system and if your system is not installed how it was explained or not up to a trades standard we will return to make any the necessary modifications free of charge. We back this service up with our 0% upfront strategy, the power is in your hands. We will only invoice you once the installation has been completed up to a BRAMBLE WORKS standard.

LOW PRESSURE SALES
Nobody likes the vacuum salesmen’s techniques and neither do we. We will come to your home or business to provide a free measure and quote. Our experience will insure this is a quick and painless experience, you will be provided with expert advice from a qualified Refrigeration Engineer, not a car salesmen turned “Heating Guru”. We will follow up with an email providing our best price straight up, installation details and online brochures. We won’t bug you with repeated phone calls and inbox clogging emails. Once we receive confirmation we will issue you with an installation date and typically have your installation completed within 10 working days.

BRANDS
www.talvoromecha.co.nz
www.pelnor.co.nz
http://quellaro.co.nz/

SERVICES
Heatpumps/Air Conditioning – Heat pumps are the most efficient way of using electricity to heat your home, but some are more efficient than others. We will select the right model for your requirements taking into account the capacity required, the visual impact of the system, the style of system, air flow and obviously your personal preferences. We only install the highest quality brands that offer outstanding after sales support. Cassettes, Consoles, Under Ceilings, Ducted, Hiwalls, Multis… Confused? Give us a call.

COMMERCIAL
We have a growing Portfolio of clients that rely on us for their Commercial requirements. We have proven ourselves to be a force to be reckoned with to be able to think outside the square and come up with unique and cost effective solutions to heat and cool large areas.

CENTRAL HEATING
Ducted Heatpumps are the holy grail of central heating and guess what? They can also cool and dehumidify your home. Ducted Heatpumps are often overlooked or priced out of reach by less experienced salesmen as its not just a point and shoot approach. We pride ourselves in our work with Ducted systems, we are able to provide quick and economic quotations and can provide expert advice on all the extra options on Ducted systems with zone control, fresh air integration, positive pressure solutions. We use the best materials when it comes to insulated ducting, mounting equipment, drainage materials. Every system we design is designed with the lowest possible decibel reading, least amount of static pressure and maximum effieciency with the help of the very latest software available.

VENTILATION
Home ventilation is a very important part of insuring you have a nice dry home to maximise the efficiency of your Heat pump. Whilst HRV systems are not designed to Heat your house they are designed to keep it dry, provide fresh filtered air to ensure your home healthy and easy to heat. We offer a number of solutions from integrated ducted heatpump systems to balanced heat recovery systems and positive air systems.

TESTIMONIALS
http://www.lotbazaro.co.nz/Browse/Listing.aspx?id=415728306

Target Market(s)

Home Owners

Industry/Entity Type

Air Conditioning

Colors
33a6d7
ffffff

Requirements
Must have
• Could possibly use the 'O' from Bramble Works logo throughout website - see business Card
Nice to have
• Bright & Crisp - White and Blue
• Would love to have our Logo used throughout the website.

```html
<!DOCTYPE html>
<html lang="en">
<head>
<meta charset="utf-8">
<title>Bramble Works – Heating &amp; Cooling</title>
<link href="https://fonts.googleapis.com/css2?family=Roboto:wght@300;400;500;700&display=swap" rel="stylesheet">
<style>
:root{
  --blue:#33a6d7;
  --blue-bright:#29b0e2;
  --blue-light:#86cdee;
  --teal:#11506b;
  --teal-dark:#0d445c;
  --ink:#1c1c1c;
  --grey-text:#7a7a7a;
  --white:#ffffff;
  --nav:#3b3b3b;
  --dark:#161616;
  --field:#f3f3f3;
}
*{box-sizing:border-box;margin:0;padding:0}
html,body{width:1200px;height:2539px;overflow:hidden}
body{position:relative;font-family:"Roboto",Arial,sans-serif;background:var(--white);color:var(--ink)}
.abs{position:absolute}

/* Hero */
.hero{left:0;top:0;width:1200px;height:657px;background:linear-gradient(180deg,#2b2a28 0%,#3c3833 45%,#2a2622 75%,#4a4039 100%)}
.hero-shade{left:0;top:0;width:1200px;height:657px;background:radial-gradient(ellipse at 60% 45%,rgba(120,100,80,.25),rgba(0,0,0,.35))}
.topbar{left:0;top:0;width:1200px;height:105px;background:rgba(0,0,0,.35)}
.brand{left:86px;top:30px;display:flex;align-items:center;gap:12px}
.brand-mark{width:34px;height:34px;border-radius:50%;background:var(--blue-bright)}
.brand-name{font-size:30px;font-weight:700;color:var(--blue-bright);letter-spacing:1px}
.contact-item{display:flex;align-items:flex-start;gap:14px;color:var(--white);font-size:17px;line-height:24px}
.ci-address{left:620px;top:30px}
.ci-phone{left:955px;top:30px}
.mainnav{left:0;top:105px;width:1200px;height:54px;background:rgba(70,70,70,.85);display:flex;justify-content:space-around;align-items:center;padding:0 90px}
.mainnav a{color:var(--white);text-decoration:none;font-size:16px;display:flex;align-items:center;gap:7px}
.mainnav a.current{color:var(--blue-light)}
.hero-title{left:0;top:300px;width:1200px;text-align:center;font-size:52px;font-weight:500;color:var(--blue-light)}
.hero-sub{left:0;top:368px;width:1200px;text-align:center;font-size:26px;font-weight:500;color:var(--white)}
.hero-line{left:0;top:409px;width:1200px;text-align:center;font-size:21px;color:var(--white)}
.btn-start{left:486px;top:470px;width:227px;height:48px;background:var(--blue-bright);color:var(--white);font-size:21px;font-weight:500;display:flex;align-items:center;justify-content:center;border-radius:2px}

/* Welcome */
.section-title{left:0;width:1200px;text-align:center;font-size:28px;font-weight:400;color:var(--ink)}
.section-title span{color:var(--blue-bright)}
.welcome-title{top:700px}
.welcome-text{left:128px;top:752px;width:944px;text-align:center;font-size:13.5px;line-height:20px;color:var(--grey-text)}
.feature{width:330px;text-align:center}
.feature-icon{width:108px;height:108px;border-radius:50%;background:var(--blue-bright);box-shadow:0 0 0 5px #d5eef8;margin:0 auto;display:flex;align-items:center;justify-content:center}
.feature h3{margin-top:26px;font-size:17px;font-weight:500;letter-spacing:.5px}
.feature p{margin:14px auto 0;width:260px;font-size:12.5px;line-height:19px;color:var(--grey-text)}
.f1{left:72px;top:892px}.f2{left:431px;top:892px}.f3{left:796px;top:892px}

/* Projects */
.projects{left:0;top:1193px;width:1200px;height:428px;background:var(--teal)}
.projects-title{top:1245px;color:var(--white);font-weight:500;font-size:26px}
.project{top:1323px;width:245px;height:231px;border:3px solid #2a86ad;overflow:hidden}
.project-photo{position:absolute;inset:0}
.project-cap{position:absolute;left:0;bottom:0;width:100%;height:42px;background:rgba(0,0,0,.55);color:var(--white);font-size:14.5px;display:flex;align-items:center;justify-content:center}
.p1{left:88px}.p2{left:347px}.p3{left:606px}.p4{left:865px}
.ph1{background:linear-gradient(160deg,#e8e8e6,#b8b6b2 60%,#6b6560)}
.ph2{background:linear-gradient(160deg,#8fa6b8,#5d6f80 50%,#2e3d52)}
.ph3{background:linear-gradient(160deg,#d9dcdc,#9ca3a5 55%,#3f4d4a)}
.ph4{background:linear-gradient(160deg,#6b6c70,#a7a9ad 50%,#4a3b36)}

/* Services */
.services-title{top:1660px}
.service{top:1723px;width:317px}
.service-photo{width:317px;height:186px;border:3px solid #e4e4e4}
.sp1{background:linear-gradient(160deg,#d8d4cc,#a8a49c 55%,#5e5a55)}
.sp2{background:linear-gradient(160deg,#f3f3f3,#c9cfd8 50%,#8d98ac)}
.sp3{background:linear-gradient(160deg,#c8d6e2,#6e8aa5 50%,#2a3c52)}
.service h3{margin-top:18px;font-size:17px;font-weight:500;letter-spacing:.4px}
.service p{margin-top:9px;font-size:12.5px;line-height:18px;color:var(--grey-text);text-align:justify;height:54px;overflow:hidden}
.service a{display:block;margin-top:8px;font-size:12px;color:var(--blue-bright);text-decoration:none}
.s1{left:88px}.s2{left:440px}.s3{left:794px}

/* Contact */
.contact-panel{left:0;top:2082px;width:640px;height:333px;background:linear-gradient(135deg,#2a2a2a,#1a1a1a)}
.contact-title{left:86px;top:2110px;font-size:28px;color:var(--white);font-weight:400}
.field{background:var(--field);font-size:11px;color:#555;padding:0 12px;display:flex;align-items:center}
.fd-name{left:90px;top:2172px;width:257px;height:40px}
.fd-email{left:357px;top:2172px;width:257px;height:40px}
.fd-company{left:90px;top:2222px;width:524px;height:40px}
.fd-message{left:90px;top:2271px;width:524px;height:61px;align-items:flex-start;padding-top:12px}
.btn-submit{left:91px;top:2347px;width:97px;height:34px;background:var(--blue-bright);color:var(--white);font-size:12px;display:flex;align-items:center;justify-content:center}
.map{left:640px;top:2082px;width:560px;height:333px;background:linear-gradient(135deg,#e9e9e7,#dcdcda 50%,#e6e4e0)}
.map-pin{left:879px;top:2180px}
.address-card{left:757px;top:2248px;width:323px;height:95px;background:var(--white);box-shadow:0 2px 8px rgba(0,0,0,.25);padding:12px 18px;font-size:13px;line-height:24px;color:var(--ink)}
.address-card b{font-weight:400;color:var(--blue-bright);display:inline-block;width:62px}

/* Footer */
.footer{left:0;top:2415px;width:1200px;height:124px;background:var(--dark)}
.footer-links{left:86px;top:2459px;font-size:13px;color:var(--white)}
.footer-links span{margin:0 8px}
.copyright{left:86px;top:2487px;font-size:12.5px;color:var(--white)}
.socials{left:943px;top:2453px;display:flex;gap:10px}
.social{width:34px;height:34px;border-radius:3px}
.social.s-a{background:#2a9fd8}.social.s-b{background:#d8392b}.social.s-c{background:#3a5a98}.social.s-d{background:#1a78b4}
</style>
</head>
<body>

<div class="abs hero" role="img" aria-label="Photo of a modern living room interior with sofa and brick wall"></div>
<div class="abs hero-shade"></div>
<div class="abs topbar"></div>

<div class="abs brand">
  <div class="brand-mark"></div>
  <div class="brand-name">BRAMBLE WORKS</div>
</div>

<div class="abs contact-item ci-address">
  <svg width="22" height="34" viewBox="0 0 22 34"><path d="M11 0C4.9 0 0 4.9 0 11c0 8 11 23 11 23s11-15 11-23C22 4.9 17.1 0 11 0z" fill="var(--blue-bright)"/><circle cx="11" cy="11" r="4.5" fill="#333"/></svg>
  <div>Bramble Works 27 Harlow Crescent<br>Petone Wellington</div>
</div>
<div class="abs contact-item ci-phone">
  <svg width="24" height="40" viewBox="0 0 24 40"><rect x="1.5" y="1.5" width="21" height="37" rx="4" fill="none" stroke="var(--blue-bright)" stroke-width="3"/><rect x="5" y="7" width="14" height="22" fill="var(--blue-bright)"/><circle cx="12" cy="33" r="2" fill="var(--blue-bright)"/></svg>
  <div>0800 529 174<br>(0800BRAMWKS)</div>
</div>

<nav class="abs mainnav">
  <a class="current" href="#"><svg width="15" height="14" viewBox="0 0 15 14"><path d="M7.5 0L0 7h2v7h4V9h3v5h4V7h2z" fill="currentColor"/></svg>HOME</a>
  <a href="#"><svg width="12" height="14" viewBox="0 0 12 14"><circle cx="6" cy="4" r="3.5" fill="currentColor"/><path d="M0 14c0-4 2.5-6 6-6s6 2 6 6z" fill="currentColor"/></svg>ABOUT US</a>
  <a href="#"><svg width="14" height="14" viewBox="0 0 14 14"><circle cx="7" cy="7" r="5" fill="none" stroke="currentColor" stroke-width="3" stroke-dasharray="2.5 1.4"/><circle cx="7" cy="7" r="2" fill="currentColor"/></svg>SERVICES</a>
  <a href="#"><svg width="14" height="14" viewBox="0 0 14 14"><circle cx="7" cy="7" r="5.5" fill="none" stroke="currentColor" stroke-width="3"/><circle cx="7" cy="7" r="2.5" fill="none" stroke="currentColor" stroke-width="1.5"/></svg>SUPPORT</a>
  <a href="#"><svg width="15" height="12" viewBox="0 0 15 12"><rect width="15" height="12" rx="1" fill="currentColor"/><path d="M0 1l7.5 6L15 1" fill="none" stroke="#555" stroke-width="1.3"/></svg>CONTACT</a>
</nav>

<h1 class="abs hero-title">BRAMBLE WORKS</h1>
<div class="abs hero-sub">SATISFACTION GAURANTEED</div>
<div class="abs hero-line">WHY CHOOSE BRAMBLE WORKS EXPERIENCE COUNTS</div>
<div class="abs btn-start">GET START NOW</div>

<h2 class="abs section-title welcome-title">WELCOME TO <span>BRAMBLE WORKS</span></h2>
<p class="abs welcome-text">We have a team of nationally trained and qualified Refrigeration/HVAC/Electrical Engineers and Technicians based in Petone, Wellington offering services to Wellington, Manuwatu and the Wairarapa. We are factory trained and authorised to design, service and install all major brands including Talvoro, Pelnor, Korrowane Electric, Veltrada and Osmelo units. We extend our installation warranty to match that of the manufacturer's warranty</p>

<div class="abs feature f1">
  <div class="feature-icon"><svg width="34" height="34" viewBox="0 0 34 34"><rect x="2" y="14" width="7" height="18" fill="#fff"/><path d="M11 14l7-11c3 0 4 2 3 5l-1.5 5H29c2 0 3 2 2.5 3.5L28 30c-.5 1.3-1.5 2-3 2H11z" fill="#fff"/></svg></div>
  <h3>SATISFACTION GUARANTEE</h3>
  <p>We aim to please and I put my name behind our brand! We will take care of your project from start to finish and offer a unique</p>
</div>
<div class="abs feature f2">
  <div class="feature-icon"><svg width="36" height="36" viewBox="0 0 36 36"><path d="M3 3h14l16 16-14 14L3 17z" fill="#fff"/><circle cx="10" cy="10" r="3" fill="var(--blue-bright)"/></svg></div>
  <h3>LOW PRESSURE SALES</h3>
  <p>We aim to please and I put my name behind our brand! We will take care of your project from start to finish and offer a unique</p>
</div>
<div class="abs feature f3">
  <div class="feature-icon"><svg width="32" height="36" viewBox="0 0 32 36"><path d="M2 2h14v6H8v22H2z" fill="#fff"/><path d="M10 10h13l7 7v17H10z" fill="#fff"/><path d="M23 10v7h7" fill="none" stroke="var(--blue-bright)" stroke-width="1.5"/></svg></div>
  <h3>EXPERIENCE COUNTS</h3>
  <p>We aim to please and I put my name behind our brand! We will take care of your project from start to finish and offer a unique</p>
</div>

<section class="abs projects"></section>
<h2 class="abs section-title projects-title">OUR LATEST PROJECTS</h2>
<div class="abs project p1"><div class="project-photo ph1" role="img" aria-label="Photo of insulated pipework and a boiler installation"></div><div class="project-cap">NEQUE PORRO QUISQUAM</div></div>
<div class="abs project p2"><div class="project-photo ph2" role="img" aria-label="Photo of an industrial pump room with pipes"></div><div class="project-cap">NEQUE PORRO QUISQUAM</div></div>
<div class="abs project p3"><div class="project-photo ph3" role="img" aria-label="Photo of circulation pumps on heating pipes"></div><div class="project-cap">NEQUE PORRO QUISQUAM</div></div>
<div class="abs project p4"><div class="project-photo ph4" role="img" aria-label="Photo of a technician fitting pipe work"></div><div class="project-cap">NEQUE PORRO QUISQUAM</div></div>

<h2 class="abs section-title services-title">OUR <span>SERVICES</span></h2>
<div class="abs service s1">
  <div class="service-photo sp1" role="img" aria-label="Photo of a commercial plant room with water tanks"></div>
  <h3>COMMERCIAL</h3>
  <p>We have a growing Portfolio of clients that rely on us for their Commercial requirements.We have proven ourselves to be a force to be reckoned with to be able</p>
  <a href="#">Read More »</a>
</div>
<div class="abs service s2">
  <div class="service-photo sp2" role="img" aria-label="Illustration of a house cutaway showing ducted heating"></div>
  <h3>CENTRAL HEATING</h3>
  <p>Ducted Heatpumps are the holy grail of central heating and guess what? They can also cool and dehumidify your home. Ducted Heatpumps are often overlooked</p>
  <a href="#">Read More »</a>
</div>
<div class="abs service s3">
  <div class="service-photo sp3" role="img" aria-label="Photo of exposed metal ventilation ducting"></div>
  <h3>VENTILATION</h3>
  <p>Home ventilation is a very important part of insuring you have a nice dry home to maximise the efficiency of your Heat pump. Whilst HRV systems are not designed</p>
  <a href="#">Read More »</a>
</div>

<section class="abs contact-panel"></section>
<h2 class="abs contact-title">CONTACT</h2>
<div class="abs field fd-name">Your Name</div>
<div class="abs field fd-email">Email id</div>
<div class="abs field fd-company">Company Name</div>
<div class="abs field fd-message">Your Message</div>
<div class="abs btn-submit">SUBMIT</div>

<div class="abs map" role="img" aria-label="Street map showing the Petone office location"></div>
<svg class="abs map-pin" width="40" height="54" viewBox="0 0 40 54"><path d="M20 0C9 0 0 9 0 20c0 14 20 34 20 34s20-20 20-34C40 9 31 0 20 0z" fill="#e8534a"/><circle cx="20" cy="19" r="7" fill="#fff"/></svg>
<div class="abs address-card">
  <div><b>Address :</b>27 Harlow Crescent Petone Wellington</div>
  <div><b>Phone :</b>0800 529 174 (0800BRAMWKS)</div>
  <div><b>E-mail :</b>Marta.k@bramwks.co.nz</div>
</div>

<footer class="abs footer"></footer>
<div class="abs footer-links">Privacy Policy<span>|</span>Terms of Use<span>|</span>About Us<span>|</span>Sitemap</div>
<div class="abs copyright">Copyright © 2016 All Rights</div>
<div class="abs socials">
  <div class="social s-a"></div><div class="social s-b"></div><div class="social s-c"></div><div class="social s-d"></div>
</div>

</body>
</html>
```